Re-Design my old Business Card

We need a new business card design. The current layout is lacking good design.
We manufacture building products and also offers services (www.tqconstructlabs.com.au)
I've attached the old business card to show you what we don't want.
I've also attached the new logo in two styles for you to chose from.
The final design should communicate smarter building design and lifestyle, with a clean and crisp designed card.

Target Market(s)

Architects, building companies

Industry/Entity Type

Business

Contact Information for Business Card

See attached old business cards for all details to include

Font styles to use
Sans Serif

Colors
9bcb3b

Requirements
Must have
• Clean crisp look
Nice to have
• Totally up to you

```html
<!DOCTYPE html>
<html lang="en">
<head>
<meta charset="utf-8">
<title>TQ Construct Labs — Business Card</title>
<link rel="stylesheet" href="https://fonts.googleapis.com/css2?family=Questrial&display=swap">
<style>
  :root {
    --stage: #e9e7e3;
    --card: #1e1e1e;
    --green: #9bcb3b;
    --text: #e6e6e6;
  }
  * { box-sizing: border-box; margin: 0; padding: 0; }
  html, body {
    width: 1200px; height: 716px; overflow: hidden;
    background: var(--stage);
    font-family: "Questrial", sans-serif;
  }
  .stage {
    width: 1200px; height: 716px;
    display: flex; justify-content: center; align-items: center; gap: 80px;
  }
  .card {
    position: relative;
    width: 320px; height: 600px;
    background: var(--card);
    border-radius: 4px;
    box-shadow: 0 10px 30px rgba(0,0,0,.25);
    overflow: hidden;
    padding: 34px 30px;
  }
  .content { position: relative; z-index: 1; }
  .tree-art {
    position: absolute;
    right: -8px; bottom: 16px;
    width: 180px; height: 160px;
    background: var(--green);
    border-radius: 48% 52% 40% 55% / 50% 45% 55% 50%;
  }

  /* Back side */
  .headline {
    color: var(--green);
    font-size: 15px; font-weight: 400; line-height: 1.28;
    text-transform: uppercase;
    letter-spacing: .2px;
  }
  .pitch {
    margin-top: 18px;
    color: var(--text);
    font-size: 12.5px; line-height: 1.4;
  }
  .pitch strong { color: var(--green); font-weight: 400; }
  .services {
    list-style: none;
    margin-top: 16px;
    color: var(--text);
    font-size: 12.5px; line-height: 1.55;
  }
  .services li { display: flex; align-items: center; gap: 8px; }
  .services li::before {
    content: ""; width: 8px; height: 8px; border-radius: 50%;
    background: var(--green);
  }

  /* Front side */
  .brand {
    display: flex; align-items: center; gap: 10px;
    color: var(--green);
    font-size: 19px; line-height: 1.1; letter-spacing: 1px;
    text-transform: uppercase;
  }
  .brand-square { width: 34px; height: 34px; background: var(--green); flex: none; }
  .person { margin-top: 34px; font-size: 13px; line-height: 1.35; color: var(--text); }
  .person .name, .office .label { color: var(--green); font-size: 15px; }
  .office { margin-top: 14px; font-size: 13px; line-height: 1.35; color: var(--text); }
  .contacts { margin-top: 22px; font-size: 13px; line-height: 1.5; color: var(--text); list-style: none; }
  .contacts li { display: flex; align-items: center; gap: 8px; white-space: nowrap; }
  .contacts svg { width: 12px; height: 12px; flex: none; }
  .contacts .gap { margin-top: 10px; }
</style>
</head>
<body>
<main class="stage">

  <section class="card card-back">
    <div class="content">
      <h2 class="headline">Everyone deserves smarter, safer and healthier options in building, design and lifestyle.</h2>
      <p class="pitch">If you want to live and work in environments that are scientifically proven to offer improved comfort, safety, health and sustainability then you will choose <strong>TQ Construct Labs.</strong></p>
      <ul class="services">
        <li>Energy Efficiency Consulting</li>
        <li>Insulation Manufacturer</li>
        <li>Building Science Technologies</li>
      </ul>
    </div>
    <div class="tree-art" role="img" aria-label="Green tree silhouette illustration"></div>
  </section>

  <section class="card card-front">
    <div class="content">
      <div class="brand"><span class="brand-square"></span><span>TQ Construct Labs</span></div>

      <div class="person">
        <div class="name">Marcus Hale</div>
        <div>Account Manager Qld /</div>
        <div>Northern NSW</div>
      </div>

      <div class="office">
        <div class="label">Head Office</div>
        <div>Unit 4/27 Harlow Street</div>
        <div>Kingsford, QLD 4208</div>
      </div>

      <ul class="contacts">
        <li><svg viewBox="0 0 12 12"><rect x="3" y="0.5" width="6" height="11" rx="1" fill="none" stroke="var(--green)" stroke-width="1.3"/></svg>0491 627 304</li>
        <li><svg viewBox="0 0 12 12"><path d="M2 1h3l1 3-2 1a7 7 0 0 0 3 3l1-2 3 1v3c0 .6-.5 1-1 1A10 10 0 0 1 1 2c0-.5.4-1 1-1z" fill="var(--green)"/></svg>1300 452 918</li>
        <li><svg viewBox="0 0 12 12"><rect x="1" y="5" width="10" height="6" fill="var(--green)"/><rect x="3" y="1" width="6" height="4" fill="none" stroke="var(--green)" stroke-width="1.2"/></svg>1300 452 919</li>
        <li class="gap"><svg viewBox="0 0 12 12"><rect x="0.5" y="2" width="11" height="8" fill="var(--green)"/><path d="M1 2.5l5 4 5-4" fill="none" stroke="var(--card)" stroke-width="1"/></svg>marcus@tqconstructlabs.com.au</li>
        <li><svg viewBox="0 0 12 12"><circle cx="6" cy="6" r="5.2" fill="none" stroke="var(--green)" stroke-width="1.2"/><path d="M1 6h10M6 1c-2.5 3-2.5 7 0 10M6 1c2.5 3 2.5 7 0 10" fill="none" stroke="var(--green)" stroke-width="1"/></svg>www.tqconstructlabs.com.au</li>
      </ul>
    </div>
    <div class="tree-art" role="img" aria-label="Green tree silhouette illustration"></div>
  </section>

</main>
</body>
</html>
```